Personal Blog

The wordpress blog style and layout should be similar to http://www.samfenwick.com

homepage: my photo, list of things, call to action then 3 boxes (The Blog, The Book and podcast)

Other pages: About us, Blog, Consulting, Contact

Target Market(s)

Web Marketing Consultant

Industry/Entity Type

Consulting

Colors
3277b5
33a6d7
f04a50
f68e4e
33b7a4

```html
<!DOCTYPE html>
<html lang="en">
<head>
<meta charset="utf-8">
<title>Karim Valdane – Personal Blog</title>
<link href="https://fonts.googleapis.com/css2?family=Dosis:wght@500;600;700&family=Arimo:wght@400;700&display=swap" rel="stylesheet">
<style>
:root{
  --teal:#1fa88e;
  --teal-light:#33b7a4;
  --teal-deep:#137a6a;
  --ink:#1c2a28;
  --dark:#15302c;
  --dark-2:#0f2421;
  --text:#222;
  --muted:#888;
  --line:#d6d9d9;
  --page:#f3f4f4;
  --white:#fff;
}
*{box-sizing:border-box;margin:0;padding:0}
html,body{width:680px;height:1200px;overflow:hidden}
body{background:var(--page);font-family:"Arimo",Arial,sans-serif;color:var(--text);position:relative}
.abs{position:absolute}

/* header */
.site-header{left:0;top:0;width:680px;height:80px;background:linear-gradient(100deg,var(--teal-deep),var(--teal-light) 55%,var(--teal));}
.brand{left:27px;top:20px;display:flex;align-items:center;font-family:"Dosis",sans-serif;font-weight:600;font-size:24px;color:var(--white)}
.brand-first{background:var(--dark);padding:4px 12px;border-radius:3px;margin-right:8px}
.main-nav{right:26px;top:31px;display:flex;gap:15px;font-family:"Dosis",sans-serif;font-weight:700;font-size:13.5px;color:var(--dark)}
.main-nav .active{color:var(--white)}

/* hero */
.hero-title{left:32px;top:100px;width:640px;font-family:"Dosis",sans-serif;font-weight:600;font-size:25px;line-height:30px;color:var(--ink)}
.hero-title em{font-style:normal;color:var(--teal)}
.topic-list{left:34px;top:174px;list-style:none;font-size:13px;line-height:23.5px}
.topic-list li::before{content:"›";color:var(--teal);font-weight:700;margin-right:10px}
.hero-photo{left:350px;top:145px;width:300px;height:160px;background:radial-gradient(ellipse at 65% 45%,#dbe3ec,#f3f4f4 70%)}
.divider{left:0;width:680px;height:1px;background:var(--line)}

/* quote */
.quote{left:60px;top:340px;width:560px;font-family:"Dosis",sans-serif;font-weight:600;font-size:14.5px;line-height:19px;color:var(--ink)}
.quote-mark{font-family:"Dosis",sans-serif;font-size:34px;color:#c7cccc;line-height:1}
.quote-by{left:400px;top:380px;width:220px;text-align:right;font-size:10px;color:var(--teal)}

/* feature boxes */
.feature{top:418px;width:200px;height:218px;border:1px solid #777;background:var(--white);text-align:center}
.feature-icon{position:absolute;left:57px;top:22px;width:84px;height:84px;border-radius:50%;background:var(--dark);border:5px solid #e4e7e7;box-shadow:0 0 0 1px #cfd3d3}
.feature-icon svg{position:absolute;left:18px;top:18px}
.feature h3{position:absolute;top:112px;width:100%;font-family:"Dosis",sans-serif;font-weight:700;font-size:18px;color:var(--teal)}
.feature p{position:absolute;top:140px;left:16px;right:16px;font-size:9.5px;line-height:13px}
.pill{display:inline-flex;align-items:center;gap:5px;font-size:9px;border-radius:10px;padding:2px 9px}
.feature .pill{position:absolute;left:65px;bottom:-8px;background:var(--dark);color:var(--white)}
.pill i{width:9px;height:9px;border:1px solid currentColor;border-radius:50%;display:inline-block;font-style:normal;font-size:6px;line-height:7px;text-align:center}

/* recent posts */
.section-title{left:0;top:672px;width:680px;text-align:center;font-family:"Dosis",sans-serif;font-weight:700;font-size:13px;color:var(--ink)}
.section-title::before,.section-title::after{content:"";display:inline-block;width:235px;height:1px;background:var(--line);vertical-align:middle;margin:0 12px}
.post{top:706px;width:147px;height:254px;border:1px solid #bbb;background:var(--white)}
.post-image{position:absolute;left:3px;top:3px;width:139px;height:107px}
.post h4{position:absolute;top:120px;left:12px;right:8px;font-family:"Dosis",sans-serif;font-weight:600;font-size:13px;line-height:16px;color:var(--teal)}
.post p{position:absolute;top:172px;left:12px;right:10px;font-size:9px;line-height:12px}
.post .pill{position:absolute;left:10px;top:219px;border:1px solid #333;color:#222}

/* footer */
.site-footer{left:0;top:996px;width:680px;height:204px;background:linear-gradient(120deg,var(--dark),var(--dark-2))}
.footer-title{font-family:"Dosis",sans-serif;font-weight:700;font-size:15.5px;color:var(--white)}
.footer-text{font-size:9px;line-height:12px;color:var(--white)}
.field{width:190px;height:24px;background:var(--white);border-radius:3px;font-size:9px;color:#333;padding:7px 6px}
.join{width:190px;height:27px;background:var(--teal-light);border-radius:3px;text-align:center;font-family:"Dosis",sans-serif;font-weight:700;font-size:16px;line-height:27px;color:var(--white)}
.social{display:flex;gap:10px}
.social span{width:30px;height:30px;background:#8e9a98;border-radius:3px;color:var(--dark);font-family:"Arimo",sans-serif;font-weight:700;font-size:8px;display:flex;align-items:center;justify-content:center}
.copyright{left:0;top:1173px;width:680px;text-align:center;font-size:8.5px;color:var(--white)}
.copyright a,.link{color:var(--teal-light);text-decoration:none}
</style>
</head>
<body>

<header class="site-header abs">
  <div class="brand abs"><span class="brand-first">Karim</span><span>Valdane</span></div>
  <nav class="main-nav abs">
    <span class="active">ABOUT</span><span>BLOG</span><span>CONSULTING</span><span>RESOURCES</span><span>BOOK</span><span>CONTACT</span>
  </nav>
</header>

<h1 class="hero-title abs">Test go here and <em>Product Management,</em> text here <em>Online Marketing,</em> to learn these topics:</h1>
<ul class="topic-list abs">
  <li>Product Management</li>
  <li>Customer Development</li>
  <li>Digital Marketing</li>
  <li>Branding &amp; Reputation</li>
  <li>Entreprenership</li>
</ul>
<div class="hero-photo abs" role="img" aria-label="Portrait of the consultant smiling at his desk beside a computer monitor"></div>
<div class="divider abs" style="top:309px"></div>

<div class="abs quote-mark" style="left:327px;top:308px">❞</div>
<div class="abs quote-mark" style="left:34px;top:336px;font-size:20px">❝</div>
<blockquote class="quote abs">"... I was blown away by his breadth of industry knowledge, the straight talking delivery and collaborative format. A highly recommended social media expert and thought leader..."</blockquote>
<div class="abs quote-mark" style="left:612px;top:356px;font-size:20px">❞</div>
<div class="quote-by abs">-Milo Brandt - Marketing</div>

<article class="feature abs" style="left:27px">
  <div class="feature-icon"><svg width="38" height="38" viewBox="0 0 38 38" fill="none" stroke="#fff" stroke-width="2.2"><ellipse cx="15" cy="14" rx="12" ry="9"/><path d="M8 21l-3 6 8-4"/><path d="M28 12c5 2 7 6 5 10l2 6-6-3c-4 1-8 0-10-2"/></svg></div>
  <h3>The Blog</h3>
  <p>Lorem Ipsum is simply dummy text of the printing &amp; typesetting industry. Lorem Ipsum has been industry's standard dummy text ever since the 15000s.</p>
  <span class="pill">Read More <i>›</i></span>
</article>
<article class="feature abs" style="left:240px">
  <div class="feature-icon"><svg width="38" height="38" viewBox="0 0 38 38"><path d="M9 5h20v26H11a3 3 0 0 1 0-6h18" fill="#fff"/><path d="M11 28h18v4H11z" fill="#fff"/><rect x="13" y="8" width="13" height="14" fill="#15302c"/></svg></div>
  <h3>The Blog</h3>
  <p>Lorem Ipsum is simply dummy text of the printing &amp; typesetting industry. Lorem Ipsum has been industry's standard dummy text ever since the 15000s.</p>
  <span class="pill">Read More <i>›</i></span>
</article>
<article class="feature abs" style="left:453px">
  <div class="feature-icon"><svg width="38" height="38" viewBox="0 0 38 38" fill="#fff"><circle cx="24" cy="12" r="6"/><path d="M13 31c0-8 5-12 11-12s11 4 11 12z"/><circle cx="12" cy="15" r="5"/><path d="M2 31c0-7 4-10 10-10 2 0 3 0 4 1-2 2-3 5-3 9z"/></svg></div>
  <h3>The Blog</h3>
  <p>Lorem Ipsum is simply dummy text of the printing &amp; typesetting industry. Lorem Ipsum has been industry's standard dummy text ever since the 15000s.</p>
  <span class="pill">Read More <i>›</i></span>
</article>

<div class="divider abs" style="top:662px"></div>
<h2 class="section-title abs">RECENT POSTS</h2>

<article class="post abs" style="left:27px">
  <div class="post-image" role="img" aria-label="Photo of a team meeting around a table with laptops and coffee" style="background:linear-gradient(135deg,#4a4440,#9a9690)"></div>
  <h4>Yet Another Video Post Format With Embedded Media ▪</h4>
  <p>Lorem Ipsum is simply dummy text of the printing &amp; typesetting industry.</p>
  <span class="pill">Read More <i>›</i></span>
</article>
<article class="post abs" style="left:187px">
  <div class="post-image" role="img" aria-label="Photo of business people applauding" style="background:linear-gradient(135deg,#e8e8e8,#3a3f48)"></div>
  <h4>Yet Another Video Post Format With Embedded Media ▪</h4>
  <p>Lorem Ipsum is simply dummy text of the printing &amp; typesetting industry.</p>
  <span class="pill">Read More <i>›</i></span>
</article>
<article class="post abs" style="left:347px">
  <div class="post-image" role="img" aria-label="Photo of a hand touching a digital interface" style="background:linear-gradient(135deg,#6a6e74,#2b2f35)"></div>
  <h4>Yet Another Video Post Format With Embedded Media ▪</h4>
  <p>Lorem Ipsum is simply dummy text of the printing &amp; typesetting industry.</p>
  <span class="pill">Read More <i>›</i></span>
</article>
<article class="post abs" style="left:507px">
  <div class="post-image" role="img" aria-label="Photo of hands on a desk phone and keyboard" style="background:linear-gradient(135deg,#d8d4d0,#4a4a4c)"></div>
  <h4>Yet Another Video Post Format With Embedded Media ▪</h4>
  <p>Lorem Ipsum is simply dummy text of the printing &amp; typesetting industry.</p>
  <span class="pill">Read More <i>›</i></span>
</article>

<footer class="site-footer abs">
  <h3 class="footer-title abs" style="left:27px;top:28px">ENTREPRENEUR, SPEAKER,</h3>
  <p class="footer-text abs" style="left:27px;top:55px;width:190px">Lorem Ipsum is simply dummy text of the printing &amp; typesetting industry. Lorem Ipsum has been industry's standard dummy text ever since the 15000s.</p>
  <p class="footer-text abs" style="left:27px;top:107px;width:190px">Lorem Ipsum is simply dummy text of the printing &amp; typesetting industry.</p>
  <p class="footer-text abs link" style="left:27px;top:134px">[ Read the long-winded version! ]</p>

  <h3 class="footer-title abs" style="left:239px;top:28px">JOIN MY NEW BUSINESS</h3>
  <div class="field abs" style="left:240px;top:57px">Enter your name...</div>
  <div class="field abs" style="left:240px;top:87px">Enter your email...</div>
  <div class="join abs" style="left:240px;top:120px">JOIN FOR FREE!</div>

  <h3 class="footer-title abs" style="left:453px;top:28px">CONNECT WITH ME</h3>
  <div class="social abs" style="left:453px;top:57px"><span>Nook</span><span>Flock</span><span>Feed</span><span>Reel</span></div>
  <p class="footer-text abs" style="left:453px;top:100px;width:160px;text-align:center">OR<br>Connect with via <span class="link">email</span></p>
</footer>
<p class="copyright abs">© 2014 K. Valdane <a href="#">www.karimvaldane.com</a> | All Right Reserved.</p>

</body>
</html>
```